Appraisal and Umpire Services for Property Damage Insurance Claims

I need a banner design that I can post as an advertisement on industry web pages. I would like this to be elegant and reflective of quality, integrity and professionalism.

Target Market(s)

Insurance Companies and Attorneys

Industry/Entity Type

Insurance

Contact Information for Business Card

Gordon T. Ashby
218 Birchwell Lane
PO Box 913
Clifton Park, NY 12348
gashby@meridaleclaims.com
Phone: (800) 519-4867, Ext. 2716
Direct: (315) 648-9052

Logo Text

Line One: Silver Hollow Claim Service, Inc. Line two: Appraisal and Umpire Services

Font styles to use
Serif
Sans Serif

Colors
0255a3
f78f20
faa54b
3176b5

Requirements
Must have
• New Logo and matching banner, business card and stationary.
• The colors must be orange and navy blue in the logo. I have selected them below.

```html
<!DOCTYPE html>
<html lang="en">
<head>
<meta charset="utf-8">
<title>Silver Hollow Claim Service, Inc — Stationery Set</title>
<link rel="stylesheet" href="https://fonts.googleapis.com/css2?family=Source+Sans+3:wght@300;400;600&display=swap">
<style>
  :root {
    --navy: #0255a3;
    --orange: #f78f20;
    --paper: #ffffff;
    --backdrop: #e2e2e2;
    --ink-light: #ffffff;
  }
  * { box-sizing: border-box; margin: 0; padding: 0; }
  html, body { width: 1200px; height: 640px; overflow: hidden; }
  body {
    background: var(--backdrop);
    font-family: "Source Sans 3", "Helvetica Neue", Arial, sans-serif;
    position: relative;
  }
  .piece { position: absolute; box-shadow: 0 2px 6px rgba(0,0,0,0.12); }

  /* Logo lockup */
  .logo { display: flex; align-items: flex-start; gap: 3px; color: var(--ink-light); font-weight: 300; line-height: 1; }
  .logo-mark { background: var(--orange); flex: none; }
  .logo-name { display: flex; flex-direction: column; }

  /* Contact block */
  .contact { line-height: 1.15; font-weight: 300; }
  .contact-title { font-weight: 600; }

  /* Folder back sheet */
  .folder { left: 60px; top: 110px; width: 296px; height: 408px; background: var(--navy); }
  .folder .logo { position: absolute; left: 38px; bottom: 38px; font-size: 13px; }
  .folder .logo-mark { width: 7px; height: 7px; margin-top: 3px; }

  /* Letterhead */
  .letterhead { left: 280px; top: 155px; width: 292px; height: 416px; background: var(--paper); }
  .letterhead-band {
    position: absolute; left: 0; bottom: 6px; width: 120px; height: 30px;
    background: var(--navy); padding: 5px 0 0 14px;
  }
  .letterhead .logo { font-size: 9px; }
  .letterhead .logo-mark { width: 5px; height: 5px; margin-top: 2px; }
  .letterhead .contact {
    position: absolute; left: 134px; bottom: 8px; color: var(--navy); font-size: 5px;
  }

  /* Envelope */
  .envelope { left: 592px; top: 46px; width: 328px; height: 127px; background: var(--navy); }
  .envelope .logo { position: absolute; left: 15px; top: 90px; font-size: 9px; }
  .envelope .logo-mark { width: 5px; height: 5px; margin-top: 2px; }
  .envelope .contact { position: absolute; left: 109px; top: 92px; color: var(--ink-light); font-size: 4.5px; opacity: 0.85; }

  /* Business card */
  .card { left: 682px; top: 312px; width: 270px; height: 155px; background: var(--navy); }
  .card .logo { position: absolute; left: 87px; top: 26px; font-size: 17px; }
  .card .logo-mark { width: 9px; height: 9px; margin-top: 3px; }
  .card .contact { position: absolute; left: 29px; top: 101px; color: var(--ink-light); font-size: 8.5px; }
</style>
</head>
<body>

  <section class="piece folder" aria-label="Folder cover">
    <div class="logo">
      <span class="logo-mark"></span>
      <span class="logo-name"><span>Silver Hollow</span><span>Claim Service, Inc</span></span>
    </div>
  </section>

  <section class="piece letterhead" aria-label="Letterhead">
    <div class="letterhead-band">
      <div class="logo">
        <span class="logo-mark"></span>
        <span class="logo-name"><span>Silver Hollow</span><span>Claim Service, Inc</span></span>
      </div>
    </div>
    <div class="contact">
      <p class="contact-title">Contact</p>
      <p>Gordon T. Ashby</p>
      <p>Email: gashby@meridaleclaims.com</p>
      <p>Phone: (800) 519-4867, Ext. 2716</p>
    </div>
  </section>

  <section class="piece envelope" aria-label="Envelope">
    <div class="logo">
      <span class="logo-mark"></span>
      <span class="logo-name"><span>Silver Hollow</span><span>Claim Service, Inc</span></span>
    </div>
    <div class="contact">
      <p class="contact-title">Contact</p>
      <p>Gordon T. Ashby</p>
      <p>Email: gashby@meridaleclaims.com</p>
      <p>Phone: (800) 519-4867, Ext. 2716</p>
    </div>
  </section>

  <section class="piece card" aria-label="Business card">
    <div class="logo">
      <span class="logo-mark"></span>
      <span class="logo-name"><span>Silver Hollow</span><span>Claim Service, Inc</span></span>
    </div>
    <div class="contact">
      <p class="contact-title">Contact</p>
      <p>Gordon T. Ashby</p>
      <p>Email: gashby@meridaleclaims.com</p>
      <p>Phone: (800) 519-4867, Ext. 2716</p>
    </div>
  </section>

</body>
</html>
```